design a construction company business card

Design business card around our logo. Card must have all the typical info: name, title, address, phone, email, business name, etc. Somewhere on the card I would like to see our motto "Grounded in Trust... Driven by Dedication." Consider adding a splash of bright orange to the card to complement the blues and silvers/grays in the logo. We are open to metallic inks, textures, etc. We would like to see options on both light and dark backgrounds. The font in the logo is Euro Technic Extended Regular.

```html
<!DOCTYPE html>
<html lang="en">
<head>
<meta charset="utf-8">
<title>Ridgeline Builders – Business Card</title>
<link rel="stylesheet" href="https://fonts.googleapis.com/css2?family=Open+Sans:wght@300;400;600;700&display=swap">
<style>
  :root {
    --bg: #d9d9d9;
    --paper: #ffffff;
    --ink: #2b2b2b;
    --brand-blue: #1f5fbf;
    --brand-blue-deep: #1b3fa0;
    --silver: #8a8a8a;
    --night: #151515;
    --night-edge: #0a0a0a;
  }
  * { box-sizing: border-box; margin: 0; padding: 0; }
  html, body { width: 1200px; height: 900px; overflow: hidden; }
  body {
    background: var(--bg);
    font-family: "Open Sans", Arial, sans-serif;
    display: flex;
    align-items: center;
    justify-content: center;
    gap: 40px;
  }
  .card {
    width: 540px;
    height: 309px;
    position: relative;
    overflow: hidden;
    box-shadow: 0 6px 18px rgba(0,0,0,0.18);
  }

  /* Front */
  .card-front { background: var(--paper); color: var(--ink); }
  .tab-marker {
    position: absolute; left: 0; top: 26px;
    width: 8px; height: 24px; background: var(--brand-blue);
  }
  .identity { position: absolute; left: 30px; top: 22px; }
  .person-name { font-size: 22px; color: var(--brand-blue); letter-spacing: 0.5px; }
  .person-name .first { font-weight: 700; text-transform: uppercase; }
  .person-name .last { font-weight: 400; }
  .person-title { font-size: 13px; font-weight: 400; margin-top: 2px; }
  .person-title .company { color: var(--brand-blue); }

  .contact-list { position: absolute; left: 30px; top: 96px; list-style: none; }
  .contact-list li {
    display: flex; align-items: center; gap: 10px;
    font-size: 13.5px; line-height: 1; margin-bottom: 9px;
  }
  .contact-icon {
    width: 18px; height: 18px; border-radius: 50%;
    background: var(--brand-blue);
    display: flex; align-items: center; justify-content: center;
    flex: none;
  }
  .contact-icon svg { width: 10px; height: 10px; }

  .wordmark {
    position: absolute; right: 34px; top: 118px;
    display: flex; align-items: center; gap: 10px;
  }
  .wordmark-square { width: 16px; height: 16px; background: var(--brand-blue); }
  .wordmark-name {
    font-size: 30px; font-weight: 700; color: var(--brand-blue-deep);
    letter-spacing: 2px; text-transform: uppercase;
  }

  .address {
    position: absolute; right: 34px; bottom: 28px;
    font-size: 13.5px; line-height: 1.45; text-align: right;
  }

  /* Back */
  .card-back {
    background: radial-gradient(ellipse at 50% 30%, #262626 0%, var(--night) 55%, var(--night-edge) 100%);
  }
  .back-wordmark {
    position: absolute; left: 0; right: 0; top: 112px;
    text-align: center;
    font-size: 30px; font-weight: 700; color: var(--brand-blue);
    letter-spacing: 3px; text-transform: uppercase;
  }
  .rule-line {
    position: absolute; left: 28px; right: 28px; top: 168px;
    height: 3px; background: var(--brand-blue-deep);
  }
  .motto {
    position: absolute; left: 0; right: 0; top: 180px;
    text-align: center;
    font-size: 12.5px; font-weight: 300; color: var(--silver);
    letter-spacing: 0.4px;
  }
</style>
</head>
<body>

  <section class="card card-front" aria-label="Business card, front">
    <div class="tab-marker"></div>
    <div class="identity">
      <h1 class="person-name"><span class="first">Marcus</span> <span class="last">hale</span></h1>
      <p class="person-title">CEO of <span class="company">Ridgeline Builders, Inc</span></p>
    </div>

    <ul class="contact-list">
      <li>
        <span class="contact-icon">
          <svg viewBox="0 0 10 10"><path d="M2 1 L4 1 L4.6 3 L3.5 3.8 Q4.5 5.8 6.2 6.5 L7 5.4 L9 6 L9 8 Q8.5 9 7.5 9 Q1 8 1 2 Q1 1 2 1 Z" fill="#fff"/></svg>
        </span>
        (02) 5550 1234
      </li>
      <li>
        <span class="contact-icon">
          <svg viewBox="0 0 10 10"><rect x="2.5" y="0.5" width="5" height="9" rx="1" fill="#fff"/><rect x="3.3" y="1.5" width="3.4" height="6" fill="#1f5fbf"/></svg>
        </span>
        0400 555 218
      </li>
      <li>
        <span class="contact-icon">
          <svg viewBox="0 0 10 10"><rect x="0.5" y="2" width="9" height="6" fill="#fff"/><path d="M0.5 2 L5 5.5 L9.5 2" fill="none" stroke="#1f5fbf" stroke-width="0.9"/></svg>
        </span>
        info@ridgelinebuilders.com
      </li>
      <li>
        <span class="contact-icon">
          <svg viewBox="0 0 10 10"><circle cx="5" cy="5" r="4" fill="none" stroke="#fff" stroke-width="1"/><ellipse cx="5" cy="5" rx="1.8" ry="4" fill="none" stroke="#fff" stroke-width="0.8"/><line x1="1" y1="5" x2="9" y2="5" stroke="#fff" stroke-width="0.8"/></svg>
        </span>
        www.ridgelinebuilders.com
      </li>
    </ul>

    <div class="wordmark">
      <span class="wordmark-square"></span>
      <span class="wordmark-name">Ridgeline</span>
    </div>

    <p class="address">18/4 Harbour Rd, Lindfield<br>NSW 2070</p>
  </section>

  <section class="card card-back" aria-label="Business card, back">
    <p class="back-wordmark">Ridgeline</p>
    <div class="rule-line"></div>
    <p class="motto">Grounded in Trust... Driven by Dedication</p>
  </section>

</body>
</html>
```